Business card for medical clinic

I need an upmarket, modern medical/health business card for my clinic

Contact Information for Business Card

name, address, email, qr code

```html
<!DOCTYPE html>
<html lang="en">
<head>
<meta charset="utf-8">
<title>Meridian Care Partners – Business Card</title>
<link href="https://fonts.googleapis.com/css2?family=Montserrat:wght@400;500;700&display=swap" rel="stylesheet">
<style>
  :root {
    --page-bg: #e8e6e2;
    --card-white: #ffffff;
    --card-navy: #1d2742;
    --brand-blue: #2a6f9e;
    --brand-sky: #2aa3dc;
    --brand-deep: #1b3a5c;
    --ink: #1a1a1a;
    --icon-blue: #2f9ad6;
    --emboss-blue: #3550a8;
  }
  * { margin: 0; padding: 0; box-sizing: border-box; }
  html, body { width: 900px; height: 1200px; overflow: hidden; }
  body {
    background: var(--page-bg);
    font-family: "Montserrat", sans-serif;
    position: relative;
  }
  .card {
    position: absolute;
    border-radius: 24px;
    box-shadow: 0 6px 18px rgba(0,0,0,0.18);
  }
  .card-front { left: 80px; top: 130px; width: 742px; height: 442px; background: var(--card-white); }
  .card-back { left: 78px; top: 637px; width: 744px; height: 441px; background: var(--card-navy); }

  .brand-mark { position: absolute; display: flex; align-items: center; gap: 12px; }
  .brand-mark .dot { border-radius: 50%; flex: none; }
  .brand-mark .brand-name { font-weight: 700; letter-spacing: 0.5px; }

  .card-front .brand-mark { left: 30px; top: 70px; }
  .card-front .dot { width: 26px; height: 26px; background: var(--brand-sky); }
  .card-front .brand-name { font-size: 19px; color: var(--brand-deep); }

  .holder { position: absolute; right: 62px; top: 48px; text-align: right; }
  .holder-name { font-size: 25px; font-weight: 700; color: var(--brand-blue); line-height: 1.2; }
  .holder-title { font-size: 15.5px; font-weight: 500; color: var(--ink); margin-top: 2px; }

  .address { position: absolute; left: 47px; top: 248px; font-size: 16px; line-height: 20px; color: var(--ink); }

  .contacts { position: absolute; left: 47px; top: 315px; list-style: none; }
  .contacts li { display: flex; align-items: center; gap: 10px; height: 31px; font-size: 16px; color: var(--ink); }
  .contacts svg { width: 17px; height: 17px; flex: none; }

  .accent-circle { position: absolute; left: 412px; top: 155px; width: 280px; height: 275px; }

  .card-back .brand-mark { left: 150px; top: 175px; gap: 18px; }
  .card-back .dot { width: 46px; height: 46px; background: var(--emboss-blue); opacity: 0.7; }
  .card-back .brand-name { font-size: 42px; color: #273665; letter-spacing: 2px; }
</style>
</head>
<body>
  <section class="card card-front" aria-label="Business card front">
    <div class="brand-mark">
      <span class="dot"></span>
      <span class="brand-name">MERIDIAN CARE PARTNERS</span>
    </div>

    <div class="holder">
      <p class="holder-name">Daniel Reyes</p>
      <p class="holder-title">Managing Director</p>
    </div>

    <p class="address">245 Cedar Ridge Lane<br>Brookfield, MS 39200</p>

    <ul class="contacts">
      <li>
        <svg viewBox="0 0 24 24"><path fill="var(--icon-blue)" d="M6.6 10.8a15.1 15.1 0 0 0 6.6 6.6l2.2-2.2c.3-.3.7-.4 1-.2 1.1.4 2.3.6 3.6.6.6 0 1 .4 1 1V20c0 .6-.4 1-1 1A17 17 0 0 1 3 4c0-.6.4-1 1-1h3.5c.6 0 1 .4 1 1 0 1.3.2 2.5.6 3.6.1.3 0 .7-.2 1z"/></svg>
        555.012.3470
      </li>
      <li>
        <svg viewBox="0 0 24 24"><path fill="var(--icon-blue)" d="M3 6h18v12H3z"/><path fill="none" stroke="#fff" stroke-width="1.6" d="M3 6l9 7 9-7"/></svg>
        hello@meridiancare.com
      </li>
      <li>
        <svg viewBox="0 0 24 24"><circle cx="12" cy="12" r="9" fill="var(--icon-blue)"/><path fill="none" stroke="#fff" stroke-width="1.2" d="M3 12h18M12 3c3 3 3 15 0 18M12 3c-3 3-3 15 0 18"/></svg>
        www.meridiancare.com
      </li>
    </ul>

    <svg class="accent-circle" role="img" aria-label="Large decorative brand accent area" viewBox="0 0 280 275">
      <defs>
        <linearGradient id="accentFill" x1="0" y1="0" x2="1" y2="1">
          <stop offset="0" stop-color="#1b3a5c" stop-opacity="0.10"/>
          <stop offset="1" stop-color="#2aa3dc" stop-opacity="0.22"/>
        </linearGradient>
      </defs>
      <circle cx="140" cy="137" r="132" fill="url(#accentFill)"/>
    </svg>
  </section>

  <section class="card card-back" aria-label="Business card back">
    <div class="brand-mark">
      <span class="dot"></span>
      <span class="brand-name">MERIDIAN CARE</span>
    </div>
  </section>
</body>
</html>
```